Business Card for a mobile physiotherapy company

I need a layout for a business card for a mobile physiotherapy company.
Slogan is "Mobile Physiotherapy - Your Road To Recovery"
Phone number is 867-555-0142
Email VardenTherapy@postnest.ca (subject to change with website)
Website www.VardenTherapy.ca
My name and credentials: Luke Varden Luke Varden, BSc(kin), MPT, CAFCI, IMS
Information maybe included: Direct Billing, Services including Physiotherapy, IMS, acupuncture
Maybe include facebook and instagram logos
One side with the logo clean and sharp
Other side with details, try not to look too busy, keep everything concise

```html
<!DOCTYPE html>
<html lang="en">
<head>
<meta charset="utf-8">
<title>Varden Therapy – Business Card</title>
<link rel="stylesheet" href="https://fonts.googleapis.com/css2?family=Noto+Serif:wght@400;700&family=Roboto:ital,wght@0,400;1,400&display=swap">
<style>
  :root {
    --navy: #2f4d80;
    --green: #0d5449;
    --white: #ffffff;
    --grey-text: #555b63;
    --backdrop: #2c2d2f;
    --card-w: 760px;
    --card-h: 434px;
  }
  * { box-sizing: border-box; margin: 0; padding: 0; }
  html, body {
    width: 1200px; height: 1108px; overflow: hidden;
    background: var(--backdrop);
  }
  .sheet {
    width: 1200px; height: 1108px;
    display: flex; flex-direction: column; align-items: center; justify-content: center;
    gap: 60px;
  }
  .card {
    width: var(--card-w); height: var(--card-h);
    background: var(--white);
    position: relative; overflow: hidden;
    box-shadow: 0 10px 30px rgba(0,0,0,.45);
  }

  /* Front */
  .card--front {
    display: flex; flex-direction: column; align-items: center; justify-content: center;
  }
  .brand {
    display: flex; align-items: center; gap: 16px;
    font-family: "Noto Serif", serif; font-weight: 700;
    color: var(--navy); font-size: 46px; letter-spacing: 4px; text-transform: uppercase;
  }
  .brand__mark { width: 22px; height: 22px; background: var(--green); }
  .slogan {
    margin-top: 34px;
    font-family: "Roboto", sans-serif; font-style: italic;
    font-size: 19px; color: var(--grey-text); letter-spacing: .3px;
  }
  .services {
    margin-top: 8px;
    font-family: "Roboto", sans-serif;
    font-size: 21px; color: var(--green);
  }
  .services .dot { color: var(--navy); padding: 0 4px; }

  /* Back */
  .card--back { display: flex; }
  .back__stripe { width: 16px; background: var(--navy); flex: none; }
  .back__details { flex: 1; padding: 40px 0 0 46px; position: relative; }
  .social { display: flex; gap: 10px; margin-left: 210px; }
  .social__dot { width: 30px; height: 30px; border-radius: 50%; background: var(--navy); }
  .person { margin-top: 52px; font-family: "Noto Serif", serif; }
  .person__name {
    font-size: 27px; font-weight: 700; color: var(--navy);
    text-transform: uppercase; letter-spacing: .5px;
  }
  .person__creds { font-size: 19px; color: var(--navy); margin-top: 2px; }
  .person__billing { font-size: 19px; color: var(--green); margin-top: 2px; }
  .contact { list-style: none; margin-top: 26px; font-family: "Noto Serif", serif; }
  .contact li {
    display: flex; align-items: center; gap: 10px;
    font-size: 18px; color: #2d3138; line-height: 1.55;
  }
  .contact svg { width: 16px; height: 16px; flex: none; fill: var(--navy); }

  .back__panel {
    width: 262px; flex: none; background: var(--green);
    display: flex; align-items: center; justify-content: center;
  }
  .panel__name {
    writing-mode: vertical-rl;
    font-family: "Noto Serif", serif; font-weight: 700;
    color: var(--white); text-transform: uppercase;
    font-size: 40px; letter-spacing: 8px; line-height: 1.3;
    text-align: center;
  }
</style>
</head>
<body>
<main class="sheet">

  <section class="card card--front" aria-label="Card front">
    <div class="brand"><span class="brand__mark"></span>Varden Therapy</div>
    <p class="slogan">Mobile Physiotherapy - Your Road To Recovery</p>
    <p class="services">Physiotherapy<span class="dot">•</span>IMS<span class="dot">•</span>Acupuncture</p>
  </section>

  <section class="card card--back" aria-label="Card back">
    <div class="back__stripe"></div>
    <div class="back__details">
      <div class="social" aria-label="Social links">
        <span class="social__dot"></span><span class="social__dot"></span>
      </div>
      <div class="person">
        <h1 class="person__name">Luke Varden</h1>
        <p class="person__creds">BSc(kin), MPT, CAFCI, IMS</p>
        <p class="person__billing">Direct Billing</p>
      </div>
      <ul class="contact">
        <li>
          <svg viewBox="0 0 24 24" aria-hidden="true"><path d="M6.6 10.8a15.1 15.1 0 0 0 6.6 6.6l2.2-2.2c.3-.3.7-.4 1-.2 1.1.4 2.3.6 3.6.6.6 0 1 .4 1 1V20c0 .6-.4 1-1 1A17 17 0 0 1 3 4c0-.6.4-1 1-1h3.5c.6 0 1 .4 1 1 0 1.3.2 2.5.6 3.6.1.3 0 .7-.2 1z"/></svg>
          867-555-0142
        </li>
        <li>
          <svg viewBox="0 0 24 24" aria-hidden="true"><path d="M2 5h20v14H2zm2 2v.4l8 5 8-5V7zm0 2.8V17h16V9.8l-8 5z"/></svg>
          VardenTherapy@postnest.ca
        </li>
        <li>
          <svg viewBox="0 0 24 24" aria-hidden="true"><path d="M12 2a10 10 0 1 0 0 20 10 10 0 0 0 0-20zm6.9 6h-3a15.7 15.7 0 0 0-1.3-3.9A8 8 0 0 1 18.9 8zM12 4c.8 1.2 1.5 2.5 1.9 4h-3.8c.4-1.5 1.1-2.8 1.9-4zM4.3 14a8.2 8.2 0 0 1 0-4h3.4a16 16 0 0 0 0 4zm.8 2h3a15.7 15.7 0 0 0 1.3 3.9A8 8 0 0 1 5.1 16zm3-8h-3a8 8 0 0 1 4.3-3.9A15.7 15.7 0 0 0 8.1 8zM12 20c-.8-1.2-1.5-2.5-1.9-4h3.8c-.4 1.5-1.1 2.8-1.9 4zm2.3-6H9.7a14.6 14.6 0 0 1 0-4h4.6a14.6 14.6 0 0 1 0 4zm.3 5.9c.6-1.2 1-2.5 1.3-3.9h3a8 8 0 0 1-4.3 3.9zM16.3 14a16 16 0 0 0 0-4h3.4a8.2 8.2 0 0 1 0 4z"/></svg>
          www.VardenTherapy.ca
        </li>
      </ul>
    </div>
    <div class="back__panel">
      <p class="panel__name">Varden<br>Therapy</p>
    </div>
  </section>

</main>
</body>
</html>
```